Southern Plantskills Academy needs a modern website that oozes professionalism

Our current website is boring and looks like everyone elses. We need a modern website that says we are the best at plant operator training. We use Brontovex and Hiraketo equipment for our training. We train all over Australia in Civil Construction, Mining and Quarrying. We want to be the "Go to" website for all plant operator training in Australia.

Industry/Entity Type

Heavy Machinery Training

Colors
0054AA
0677BA
7BADD7
CADEEF
E8F1F8
FFF300
FFF600
FEFA6F
FFFEC7
FFFEE8

```html
<!DOCTYPE html>
<html lang="en">
<head>
<meta charset="utf-8">
<title>Southern Plantskills Academy</title>
<link rel="stylesheet" href="https://fonts.googleapis.com/css2?family=Open+Sans:wght@400;600;700;800&family=Tinos:wght@400;700&display=swap">
<style>
:root{
  --navy:#0d3461;
  --navy-deep:#0a2a50;
  --blue:#0054AA;
  --yellow:#F6C400;
  --yellow-soft:#FFF600;
  --lavender:#efedf7;
  --lavender-2:#e3e0f1;
  --ink:#1f2433;
  --muted:#6b7080;
  --white:#ffffff;
  --footer:#1d232e;
  --sans:'Open Sans',Arial,sans-serif;
  --serif:'Tinos','Times New Roman',serif;
}
*{box-sizing:border-box;margin:0;padding:0}
html,body{width:1200px;height:5068px;overflow:hidden}
body{position:relative;font-family:var(--sans);color:var(--ink);background:var(--white)}
.abs{position:absolute}
.section{position:absolute;left:0;width:1200px}
.serif{font-family:var(--serif)}
.center{text-align:center}

/* header */
.site-header{top:0;height:120px;background:var(--white)}
.contact-chip{position:absolute;top:22px;display:flex;align-items:center;gap:10px}
.chip-icon{width:34px;height:34px;border-radius:50%;background:var(--navy);display:flex;align-items:center;justify-content:center}
.chip-label{font-size:13px;font-weight:700;color:var(--ink)}
.chip-value{font-size:11px;color:var(--muted)}
.brand{position:absolute;left:480px;top:18px;width:240px;display:flex;align-items:center;gap:10px;justify-content:center}
.brand-dot{width:46px;height:46px;border-radius:50%;background:var(--yellow)}
.brand-name{font-family:var(--sans);font-weight:800;font-size:16px;line-height:1.1;color:var(--navy);text-transform:uppercase}
.brand-line{position:absolute;left:500px;top:72px;width:200px;height:3px;background:var(--yellow)}
.btn-book{position:absolute;left:890px;top:16px;width:180px;height:40px;border-radius:20px;background:var(--navy);color:var(--white);font-size:12px;font-weight:700;display:flex;align-items:center;justify-content:center}
.main-nav a{position:absolute;top:80px;font-size:13px;color:var(--ink);text-decoration:none}

/* hero */
.hero{top:120px;height:780px;background:linear-gradient(120deg,#3a3d42 0%,#5b5650 45%,#7a6a50 75%,#4b4740 100%)}
.hero-photo{position:absolute;inset:0;background:radial-gradient(ellipse at 78% 52%,rgba(214,160,60,.55),transparent 40%),linear-gradient(180deg,rgba(0,0,0,.15),rgba(0,0,0,.45))}
.hero-welcome{position:absolute;left:80px;top:240px;font-size:22px;font-weight:700;letter-spacing:4px;color:var(--white)}
.hero-title{position:absolute;left:80px;top:286px;font-size:50px;font-weight:700;color:var(--white)}
.hero-rule{position:absolute;left:80px;top:366px;width:700px;height:2px;background:rgba(255,255,255,.7)}
.hero-text{position:absolute;left:80px;top:392px;width:640px;font-size:17px;line-height:1.5;color:var(--white)}
.btn{position:absolute;height:44px;border-radius:22px;font-size:13px;font-weight:700;display:flex;align-items:center;justify-content:center}
.btn-yellow{background:var(--yellow);color:var(--ink)}
.btn-white{background:var(--white);color:var(--navy)}
.hero-curve{position:absolute;left:0;top:640px}
.badge{position:absolute;left:568px;width:64px;height:64px;border-radius:50%;background:var(--white);border:3px solid var(--navy);display:flex;align-items:center;justify-content:center}
.badge span{width:26px;height:26px;border-radius:50%;background:var(--yellow)}

/* about */
.about{top:900px;height:612px}
.about-photo{position:absolute;left:140px;top:60px;width:400px;height:400px;border-radius:50%;background:linear-gradient(160deg,#9fb5c8,#8a7a55 55%,#c79a3b);border:10px solid var(--white);box-shadow:0 0 0 6px var(--yellow)}
.eyebrow{font-size:15px;color:var(--yellow);font-weight:600}
.about-title{position:absolute;left:620px;top:108px;width:480px;font-family:var(--serif);font-size:34px;line-height:1.25;color:var(--navy)}
.about-lead{position:absolute;left:620px;top:226px;width:480px;padding:10px 16px;border-left:4px solid var(--navy);background:var(--lavender);font-size:14px;line-height:1.5;color:var(--muted)}
.about-text{position:absolute;left:620px;top:310px;width:480px;font-size:14px;line-height:1.6;color:var(--muted)}

/* services */
.services{top:1512px;height:568px;background:var(--lavender)}
.sec-title{position:absolute;left:0;width:1200px;text-align:center;font-family:var(--serif);font-size:44px;color:var(--navy)}
.sec-sub{position:absolute;left:360px;width:480px;text-align:center;font-size:14px;line-height:1.5;color:var(--muted)}
.service-card{position:absolute;top:236px;width:316px;height:272px;border-radius:6px;overflow:hidden}
.service-card .icon{position:absolute;left:24px;top:20px;width:44px;height:44px;border-radius:50%;border:2px solid var(--yellow);background:rgba(255,255,255,.15);display:flex;align-items:center;justify-content:center}
.service-card h3{position:absolute;left:20px;top:82px;font-family:var(--serif);font-size:30px;color:var(--white);font-weight:700}
.service-card .arrow{position:absolute;left:24px;bottom:26px}

/* projects */
.projects{top:2080px;height:560px;background:var(--navy)}
.projects .sec-title,.projects .sec-sub{color:var(--white)}
.project-shot{position:absolute;border:6px solid var(--white)}
.slider-arrow{position:absolute;width:48px;height:48px;border-radius:50%;background:var(--white);display:flex;align-items:center;justify-content:center;box-shadow:0 2px 8px rgba(0,0,0,.3)}

/* why */
.why{top:2640px;height:732px}
.why-panel{position:absolute;top:210px;height:440px;width:420px;background:linear-gradient(90deg,rgba(239,237,247,0),var(--lavender))}
.why-panel.right{background:linear-gradient(270deg,rgba(239,237,247,0),var(--lavender))}
.why-person{position:absolute;left:494px;top:200px;width:212px;height:450px;border-radius:106px 106px 10px 10px;background:linear-gradient(180deg,#cbd3dc,#33455e 70%);z-index:1}
.why-item{position:absolute;width:290px;z-index:2}
.why-item h4{font-family:var(--serif);font-size:22px;color:var(--navy);font-weight:400;margin-bottom:6px;white-space:nowrap}
.why-item p{font-size:13px;line-height:1.5;color:var(--muted)}
.why-item.left{left:100px;text-align:right}
.why-item.right{left:810px}
.why-icon{position:absolute;width:60px;height:60px;border-radius:50%;background:var(--navy);border:4px solid var(--white);box-shadow:0 0 0 3px var(--lavender-2);display:flex;align-items:center;justify-content:center;z-index:3}

/* hours */
.hours{top:3372px;height:452px;background:linear-gradient(100deg,#14171d,#2a2a2a 50%,#40391f)}
.hours-bar{position:absolute;left:92px;top:140px;width:4px;height:270px;background:var(--yellow)}
.hours-title{position:absolute;left:92px;top:126px;font-family:var(--serif);font-size:30px;color:var(--white)}
.hours-row{position:absolute;left:130px;width:430px;display:flex;justify-content:space-between;font-size:14px;color:var(--white);padding-bottom:14px;border-bottom:1px solid rgba(255,255,255,.2)}
.hours-row b{font-weight:600}
.hours-row span{color:#c9c9c9}

.appointment{position:absolute;left:608px;top:3392px;width:492px;height:504px;background:var(--lavender);z-index:3;padding:24px 44px}
.appt-head{display:flex;align-items:center;gap:14px}
.appt-head .dot{width:40px;height:40px;border-radius:50%;background:var(--navy)}
.appt-head small{font-size:12px;color:var(--muted);display:block}
.appt-head h3{font-family:var(--serif);font-weight:400;font-size:32px;color:var(--navy)}
.field{position:absolute;height:56px;background:var(--white);border:1px solid #dcd9ea;font-size:13px;color:var(--ink);display:flex;align-items:center;padding:0 14px}
.submit{position:absolute;left:44px;top:424px;width:404px;height:52px;background:var(--yellow);color:var(--white);font-weight:700;font-size:15px;display:flex;align-items:center;justify-content:center}

/* reviews */
.reviews{top:3824px;height:616px;background:#f6f5fb}
.review-card{position:absolute;top:324px;width:320px;height:216px;background:var(--white);padding:20px 24px;box-shadow:0 4px 14px rgba(0,0,0,.06)}
.review-card.active{border-bottom:6px solid var(--navy)}
.avatar{width:54px;height:54px;border-radius:50%;background:linear-gradient(160deg,#c8b9a6,#7a6652)}
.quote{position:absolute;right:22px;top:18px;font-family:var(--serif);font-size:80px;line-height:.8;color:var(--yellow);font-weight:700}
.stars{color:var(--yellow);font-size:16px;letter-spacing:2px;margin-top:10px}
.review-card p{font-size:12px;line-height:1.5;color:var(--muted);margin-top:6px}
.review-card h5{font-family:var(--serif);font-size:20px;font-weight:400;color:var(--navy);margin-top:8px}
.review-card .role{font-size:11px;color:var(--yellow)}

/* footer */
.footer{top:4440px;height:568px}
.footer-logo{position:absolute;left:0;width:1200px;top:170px;display:flex;flex-direction:column;align-items:center;gap:8px}
.footer-logo .brand-name{color:var(--white);font-size:26px}
.footer-nav{position:absolute;top:384px;left:0;width:1200px;display:flex;justify-content:center;gap:52px}
.footer-nav a{color:var(--white);font-size:13px;text-decoration:none}
.footer-rule{position:absolute;left:160px;top:432px;width:880px;height:1px;background:rgba(255,255,255,.2)}
.footer-contact{position:absolute;top:478px;display:flex;align-items:center;gap:14px;color:#cfd3da;font-size:12px}
.footer-contact b{display:block;color:var(--white);font-size:13px}
.footer-sep{position:absolute;top:470px;width:1px;height:60px;background:rgba(255,255,255,.25)}
.bottom-bar{top:5008px;height:60px;background:#0d3a7c;display:flex;align-items:center;justify-content:space-between;padding:0 144px}
.bottom-bar strong{color:var(--white);font-size:14px}
.social{display:flex;gap:10px}
.social span{width:26px;height:26px;background:var(--blue);border:1px solid rgba(255,255,255,.4)}
</style>
</head>
<body>

<header class="section site-header">
  <div class="contact-chip" style="left:120px">
    <div class="chip-icon"><svg width="16" height="16" viewBox="0 0 24 24"><path d="M6.6 10.8a15 15 0 006.6 6.6l2.2-2.2a1 1 0 011-.25 11.4 11.4 0 003.6.6 1 1 0 011 1V20a1 1 0 01-1 1A17 17 0 013 4a1 1 0 011-1h3.5a1 1 0 011 1c0 1.25.2 2.45.6 3.6a1 1 0 01-.25 1z" fill="#fff"/></svg></div>
    <div><div class="chip-label">Call Us</div><div class="chip-value">+61 400 555 019</div></div>
  </div>
  <div class="contact-chip" style="left:280px">
    <div class="chip-icon"><svg width="16" height="16" viewBox="0 0 24 24"><rect x="3" y="5" width="18" height="14" rx="2" fill="#fff"/><path d="M3 6l9 7 9-7" stroke="#0d3461" stroke-width="2" fill="none"/></svg></div>
    <div><div class="chip-label">Email</div><div class="chip-value">hello@plantskills.example</div></div>
  </div>
  <div class="brand"><span class="brand-dot"></span><span class="brand-name">Southern<br>Plantskills Academy</span></div>
  <div class="brand-line"></div>
  <div class="btn-book">BOOK APPOINTMENT</div>
  <nav class="main-nav">
    <a style="left:124px">Home</a><a style="left:236px">About Us</a><a style="left:384px">Services</a>
    <a style="left:708px">Team</a><a style="left:832px">Blog</a><a style="left:950px">Contact Us</a>
  </nav>
</header>

<section class="section hero">
  <div class="hero-photo" role="img" aria-label="Excavator working on a quarry site"></div>
  <div class="hero-welcome">Welcome</div>
  <h1 class="hero-title">Best in Operator Training</h1>
  <div class="hero-rule"></div>
  <p class="hero-text">Nationally recognised plant operator courses delivered on real sites, by real operators, across every state.</p>
  <div class="btn btn-yellow" style="left:80px;top:488px;width:128px">LEARN MORE</div>
  <div class="btn btn-white" style="left:236px;top:488px;width:156px">REQUEST QUOTE</div>
  <svg class="hero-curve" width="1200" height="140" viewBox="0 0 1200 140">
    <path d="M0 30 Q600 150 1200 30 L1200 140 L0 140Z" fill="#fff"/>
    <path d="M0 44 Q600 164 1200 44" stroke="#F6C400" stroke-width="5" fill="none"/>
  </svg>
</section>
<div class="badge" style="top:856px"><span></span></div>

<section class="section about">
  <div class="about-photo" role="img" aria-label="Operator in hi-vis vest beside a wheel loader"></div>
  <div class="eyebrow abs" style="left:620px;top:70px">About Us</div>
  <h2 class="about-title">Training Operators for Industry Leaders</h2>
  <p class="about-lead">Hands-on courses on Brontovex and Hiraketo machines, taught by experienced site trainers.</p>
  <p class="about-text">We deliver plant operator training all over Australia for civil construction, mining and quarrying crews. Every course mixes practical seat time with safety theory, so your people leave site-ready and fully ticketed.</p>
  <div class="btn btn-yellow" style="left:620px;top:446px;width:150px;border-radius:4px;gap:10px">Contact us <svg width="16" height="10" viewBox="0 0 16 10"><path d="M0 5h14M10 1l4 4-4 4" stroke="#1f2433" stroke-width="1.6" fill="none"/></svg></div>
</section>

<section class="section services">
  <h2 class="sec-title" style="top:52px">Our Services</h2>
  <p class="sec-sub" style="top:114px">Accredited operator courses for every major sector, delivered on site or at our yards.</p>
  <div class="service-card" style="left:92px;background:linear-gradient(160deg,#3b4a5e,#6b6a66)" role="img" aria-label="Civil construction worker on site">
    <div class="icon"><svg width="20" height="20" viewBox="0 0 24 24"><path d="M4 16a8 8 0 0116 0zM2 16h20v3H2z" fill="#F6C400"/></svg></div>
    <h3>Civil Construction</h3>
    <svg class="arrow" width="30" height="14" viewBox="0 0 30 14"><path d="M0 7h28M22 1l6 6-6 6" stroke="#fff" stroke-width="2" fill="none"/></svg>
  </div>
  <div class="service-card" style="left:436px;background:linear-gradient(160deg,#6e5230,#a9743a)" role="img" aria-label="Mining haul trucks in an open pit">
    <div class="icon"><svg width="20" height="20" viewBox="0 0 24 24"><path d="M12 3l9 17H3z" fill="#F6C400"/></svg></div>
    <h3>Mining</h3>
    <svg class="arrow" width="30" height="14" viewBox="0 0 30 14"><path d="M0 7h28M22 1l6 6-6 6" stroke="#fff" stroke-width="2" fill="none"/></svg>
  </div>
  <div class="service-card" style="left:780px;background:linear-gradient(160deg,#8a6a3a,#c8a060)" role="img" aria-label="Quarry with gravel stockpiles">
    <div class="icon"><svg width="20" height="20" viewBox="0 0 24 24"><circle cx="9" cy="15" r="6" fill="#F6C400"/><circle cx="17" cy="10" r="4" fill="#F6C400"/></svg></div>
    <h3>Quarrying</h3>
    <svg class="arrow" width="30" height="14" viewBox="0 0 30 14"><path d="M0 7h28M22 1l6 6-6 6" stroke="#fff" stroke-width="2" fill="none"/></svg>
  </div>
</section>

<section class="section projects">
  <h2 class="sec-title" style="top:52px">Recent Projects</h2>
  <p class="sec-sub" style="top:114px;color:#cfd6e2">A look at recent crews we have trained on live civil, mining and quarry sites.</p>
  <div class="project-shot" style="left:124px;top:220px;width:200px;height:300px;background:linear-gradient(160deg,#9bb0c4,#c29a40)" role="img" aria-label="Trainee operator in hard hat"></div>
  <div class="project-shot" style="left:876px;top:220px;width:200px;height:300px;background:linear-gradient(160deg,#a9bccd,#c8a02a)" role="img" aria-label="Wheel loader on a worksite"></div>
  <div class="project-shot" style="left:320px;top:196px;width:560px;height:344px;background:linear-gradient(180deg,#b8c2cb,#7c7466 55%,#5a5247);z-index:2" role="img" aria-label="Excavator levelling a muddy construction site"></div>
  <div class="slider-arrow" style="left:296px;top:344px;z-index:3"><svg width="14" height="14" viewBox="0 0 14 14"><path d="M10 1L4 7l6 6" stroke="#0d3461" stroke-width="2.4" fill="none"/></svg></div>
  <div class="slider-arrow" style="left:856px;top:344px;z-index:3"><svg width="14" height="14" viewBox="0 0 14 14"><path d="M4 1l6 6-6 6" stroke="#0d3461" stroke-width="2.4" fill="none"/></svg></div>
</section>

<section class="section why">
  <h2 class="sec-title" style="top:50px">Why Choose Us</h2>
  <p class="sec-sub" style="top:112px">Trusted by contractors nationwide for practical, safe and accredited operator training.</p>
  <div class="why-panel" style="left:80px"></div>
  <div class="why-panel right" style="left:700px"></div>
  <div class="why-person" role="img" aria-label="Smiling trainer in a suit with arms crossed"></div>

  <div class="why-item left" style="top:262px"><h4>Quality Assurance</h4><p>Every course is audited to meet national standards and site rules.</p></div>
  <div class="why-item left" style="top:394px"><h4>Proven Record</h4><p>Thousands of operators trained and placed with leading contractors.</p></div>
  <div class="why-item left" style="top:526px"><h4>Personalized Approach</h4><p>Courses shaped around your crew, your machines and your site.</p></div>
  <div class="why-item right" style="top:262px"><h4>Comprehensive Services</h4><p>From first tickets to refresher courses and on-site assessments.</p></div>
  <div class="why-item right" style="top:394px"><h4>Professionalism</h4><p>Punctual, prepared trainers who respect your schedule and safety.</p></div>
  <div class="why-item right" style="top:526px"><h4>Experience and Expertise</h4><p>Trainers with decades of seat time across all major plant types.</p></div>

  <div class="why-icon" style="left:414px;top:254px"><svg width="22" height="22" viewBox="0 0 24 24"><path d="M12 3a9 9 0 100 18 9 9 0 000-18zm0 4v5l3 3" stroke="#fff" stroke-width="2" fill="none"/></svg></div>
  <div class="why-icon" style="left:414px;top:386px"><svg width="22" height="22" viewBox="0 0 24 24"><path d="M12 2l3 7 7 .5-5.5 4.5 2 7-6.5-4-6.5 4 2-7L2 9.5 9 9z" stroke="#fff" stroke-width="1.8" fill="none"/></svg></div>
  <div class="why-icon" style="left:414px;top:518px"><svg width="22" height="22" viewBox="0 0 24 24"><circle cx="12" cy="8" r="4" stroke="#fff" stroke-width="2" fill="none"/><path d="M4 21a8 8 0 0116 0" stroke="#fff" stroke-width="2" fill="none"/></svg></div>
  <div class="why-icon" style="left:726px;top:254px"><svg width="22" height="22" viewBox="0 0 24 24"><path d="M5 12l5 5 9-10" stroke="#fff" stroke-width="2.4" fill="none"/></svg></div>
  <div class="why-icon" style="left:726px;top:386px"><svg width="22" height="22" viewBox="0 0 24 24"><rect x="4" y="7" width="16" height="12" rx="2" stroke="#fff" stroke-width="2" fill="none"/><path d="M9 7V4h6v3" stroke="#fff" stroke-width="2" fill="none"/></svg></div>
  <div class="why-icon" style="left:726px;top:518px"><svg width="22" height="22" viewBox="0 0 24 24"><path d="M20 12a8 8 0 01-14 5M4 12a8 8 0 0114-5M18 3v4h-4M6 21v-4h4" stroke="#fff" stroke-width="2" fill="none"/></svg></div>
</section>

<section class="section hours" role="img" aria-label="Dark photo of heavy machinery at dusk">
  <div class="hours-bar"></div>
  <h3 class="hours-title" style="left:110px">Opening Hours</h3>
  <div class="hours-row" style="top:220px"><b>Monday - Thursday</b><span>08am - 02pm</span></div>
  <div class="hours-row" style="top:270px"><b>Saturday</b><span>08am - 02pm</span></div>
  <div class="hours-row" style="top:320px"><b>Phone</b><span>+61 400 555 019</span></div>
  <div class="hours-row" style="top:370px;border-bottom:none"><b>Email</b><span>hello@plantskills.example</span></div>
</section>

<div class="appointment">
  <div class="appt-head"><span class="dot"></span><div><small>Get in touch with us any day any time</small><h3>Make Appointment</h3></div></div>
  <div class="field" style="left:44px;top:112px;width:194px">First Name</div>
  <div class="field" style="left:254px;top:112px;width:194px">Last Name</div>
  <div class="field" style="left:44px;top:188px;width:194px">Email Address</div>
  <div class="field" style="left:254px;top:188px;width:194px">Phone Number</div>
  <div class="field" style="left:44px;top:264px;width:404px;justify-content:space-between">Select Subject<svg width="12" height="8" viewBox="0 0 12 8"><path d="M1 1l5 5 5-5" stroke="#6b7080" stroke-width="1.6" fill="none"/></svg></div>
  <div class="field" style="left:44px;top:340px;width:404px">dd/mm/yyyy</div>
  <div class="submit">SUBMIT</div>
</div>

<section class="section reviews">
  <h2 class="sec-title" style="top:180px">Clients Review</h2>
  <p class="sec-sub" style="top:242px">Hear from site managers and operators who have completed our courses.</p>
  <div class="review-card" style="left:100px">
    <div class="avatar" role="img" aria-label="Client portrait"></div><span class="quote">&#8220;</span>
    <div class="stars">&#9733;&#9733;&#9733;&#9733;&#9733;</div>
    <p>Our crew came back confident and fully ticketed. Practical, well run and genuinely useful.</p>
    <h5>Mara Delling</h5><div class="role">Site Manager</div>
  </div>
  <div class="review-card active" style="left:440px">
    <div class="avatar" role="img" aria-label="Client portrait"></div><span class="quote">&#8220;</span>
    <div class="stars">&#9733;&#9733;&#9733;&#9733;&#9733;</div>
    <p>Great trainers who know the machines inside out. Booking on site was quick and easy.</p>
    <h5>Mara Delling</h5><div class="role">Site Manager</div>
  </div>
  <div class="review-card" style="left:780px">
    <div class="avatar" role="img" aria-label="Client portrait"></div><span class="quote">&#8220;</span>
    <div class="stars">&#9733;&#9733;&#9733;&#9733;&#9733;</div>
    <p>The best operator training we have used. Clear, safe and tailored to our quarry work.</p>
    <h5>Mara Delling</h5><div class="role">Site Manager</div>
  </div>
</section>

<footer class="section footer">
  <svg class="abs" style="left:0;top:0" width="1200" height="568" viewBox="0 0 1200 568">
    <path d="M0 40 Q600 -60 1200 40 L1200 568 L0 568Z" fill="#1d232e"/>
    <path d="M0 24 Q600 -76 1200 24" stroke="#F6C400" stroke-width="5" fill="none"/>
  </svg>
  <div class="badge" style="top:20px"><span></span></div>
  <div class="footer-logo"><span class="brand-dot" style="width:60px;height:60px"></span><span class="brand-name">Southern Plantskills Academy</span></div>
  <nav class="footer-nav"><a>HOME</a><a>SERVICES</a><a>ABOUT US</a><a>TESTIMONIALS</a><a>BLOG</a></nav>
  <div class="footer-rule"></div>
  <div class="footer-contact" style="left:180px"><svg width="22" height="22" viewBox="0 0 24 24"><path d="M12 2a7 7 0 017 7c0 5-7 13-7 13S5 14 5 9a7 7 0 017-7z" stroke="#fff" stroke-width="1.8" fill="none"/><circle cx="12" cy="9" r="2.5" fill="#fff"/></svg><div>14 Quarry Road, Yard 3<br>Bendale, VIC 3999</div></div>
  <div class="footer-sep" style="left:420px"></div>
  <div class="footer-contact" style="left:500px"><svg width="22" height="22" viewBox="0 0 24 24"><path d="M6.6 10.8a15 15 0 006.6 6.6l2.2-2.2 4.6.6V20A17 17 0 013 4h4.5l.6 4.6z" stroke="#fff" stroke-width="1.8" fill="none"/></svg><div><b>PHONE</b>+61 400 555 019</div></div>
  <div class="footer-sep" style="left:760px"></div>
  <div class="footer-contact" style="left:840px"><svg width="22" height="22" viewBox="0 0 24 24"><rect x="3" y="5" width="18" height="14" rx="2" stroke="#fff" stroke-width="1.8" fill="none"/><path d="M3 6l9 7 9-7" stroke="#fff" stroke-width="1.8" fill="none"/></svg><div><b>EMAIL</b>hello@plantskills.example</div></div>
</footer>

<div class="section bottom-bar">
  <strong>Southern Plantskills Academy</strong>
  <div class="social"><span></span><span></span><span></span><span></span></div>
</div>

</body>
</html>
```